Modern Medical Optometry Website

We need mordern, Patient friendly website. Easy to navigate and enhance our advance medical technology and excellent patient care.
1. HOME PAGE
2. OUR TEAM PAGE
3. EYECARE PAGE - VISION SERVICES, EYE EXAMS, KERATOCONUS CENTER, GLAUCOMA , DIABITES, MELORIDEX EXAM, DIGITAL RETINAL, OCT.
4. MYOPIA CONTROL CLINIC
5. DRY EYE CLINIC
6. EYEWEAR
7. PATIENT CENTER - BLOG
7. CONTACT US
This is our current website www.brivaloka.com
and We want to add more content and a cleaner design like these website
http://tarnwickfolvendale.com/
https://www.qmvorlu.com/

```html
<!DOCTYPE html>
<html lang="en">
<head>
<meta charset="utf-8">
<title>Glaucoma – Lumora Optometry</title>
<link rel="stylesheet" href="https://fonts.googleapis.com/css2?family=Jost:wght@400;500&family=Mulish:wght@400;600;700;800&family=Raleway:wght@700&display=swap">
<style>
:root{
  --teal:#0e8cb0;
  --gold:#f2c21b;
  --ink:#2e2e2e;
  --muted:#8f8f8f;
  --nav:#8a8a8a;
  --band:#f0f0f0;
  --sun:#f9e05c;
  --pill:#333333;
  --white:#ffffff;
}
*{box-sizing:border-box;margin:0;padding:0}
html,body{width:886px;height:1200px;overflow:hidden;background:var(--white)}
body{position:relative;font-family:"Mulish",Arial,sans-serif;color:var(--ink)}
.abs{position:absolute}

.topbar{left:0;top:0;width:886px;height:38px;background:var(--teal);color:var(--white)}
.topbar .cell{position:absolute;top:0;height:38px;border-left:1px solid rgba(255,255,255,.25);display:flex;align-items:center;font-size:11px;gap:9px;white-space:nowrap}
.topbar .cell:last-child{border-right:1px solid rgba(255,255,255,.25)}
.topbar .sq{width:38px;justify-content:center}
.dot{width:7px;height:7px;border-radius:50%;background:var(--gold)}

.brand{left:57px;top:15px;width:81px;height:104px;background:var(--white);display:flex;flex-direction:column;align-items:center;justify-content:center;gap:8px}
.brand .mark{width:34px;height:34px;background:var(--gold)}
.brand .name{font-family:"Jost",sans-serif;font-size:11px;color:var(--nav);letter-spacing:.5px}
.nav{left:163px;top:82px;font-family:"Jost",sans-serif;font-size:12.5px;color:var(--nav)}
.nav a{position:absolute;white-space:nowrap;text-decoration:none;color:inherit;top:0}
.nav a.current{color:var(--teal)}
.search{left:814px;top:81px}

.title-band{left:0;top:138px;width:886px;height:100px;background:var(--band);display:flex;align-items:center;justify-content:center}
.title-band h1{font-family:"Raleway",sans-serif;font-weight:700;font-size:26px;color:var(--teal);letter-spacing:.3px}

.hero{left:57px;top:278px;width:373px;height:308px;background:linear-gradient(135deg,#a57a6c 0%,#5f93c2 45%,#4d80b2 60%,#9c7467 100%)}
p{font-size:11px;line-height:19.3px}
.lead{font-weight:700;color:var(--ink)}
.body{color:var(--muted)}
.p1{left:463px;top:303px;width:335px}
.p2{left:463px;top:384px;width:330px}
.p3{left:58px;top:622px;width:368px}
.p4{left:463px;top:622px;width:370px}
.p5{left:58px;top:744px;width:780px}

.footer{left:0;top:846px;width:886px;height:354px;background:var(--sun)}
.footer h2{position:absolute;top:45px;font-size:15.5px;font-weight:700;color:var(--teal);white-space:nowrap}
.col{position:absolute;top:0;width:240px}
.item{position:absolute;left:0;display:flex;gap:16px;font-size:11px;line-height:19px;color:var(--ink);white-space:nowrap}
.item .ic{width:17px;flex:none;display:flex;justify-content:center;margin-top:2px}
.btn{position:absolute;top:231px;left:0;width:206px;height:31px;border-radius:16px;background:var(--pill);color:var(--white);font-size:11.5px;display:flex;align-items:center;padding-left:13px;gap:16px;white-space:nowrap}
.hours{position:absolute;left:0;font-size:11px;color:var(--ink);line-height:16px}
.hours b{font-weight:800;font-size:11.5px}
.social{position:absolute;top:231px;width:31px;height:31px;border-radius:50%;background:var(--pill);display:flex;align-items:center;justify-content:center}
.social.first{background:var(--teal)}
.rule{position:absolute;left:0;top:300px;width:886px;height:1px;background:rgba(0,0,0,.06)}
.copy{position:absolute;top:319px;width:886px;text-align:center;font-size:10px;color:#6b6b6b}
.copy b{color:var(--teal);font-weight:800}
</style>
</head>
<body>

<header>
  <div class="abs topbar">
    <div class="cell" style="left:342px;width:126px;padding-left:14px">
      <svg width="15" height="15" viewBox="0 0 24 24" fill="none" stroke="#f2c21b" stroke-width="1.6"><path d="M5 3l4 1 1 5-2 2a12 12 0 006 6l2-2 5 1 1 4c-1 1-2 2-4 2C10 22 2 14 2 7c0-2 1-3 3-4z"/></svg>
      <span>818-555-0142</span>
    </div>
    <div class="cell" style="left:468px;width:207px;padding-left:15px">
      <svg width="16" height="12" viewBox="0 0 24 18" fill="none" stroke="#f2c21b" stroke-width="1.6"><rect x="1" y="1" width="22" height="16"/><path d="M1 1l11 9 11-9"/></svg>
      <span>hello@lumoraoptometry.com</span>
    </div>
    <div class="cell sq" style="left:675px"><span class="dot"></span></div>
    <div class="cell sq" style="left:713px"><span class="dot"></span></div>
    <div class="cell sq" style="left:752px"><span class="dot"></span></div>
    <div class="cell sq" style="left:790px"><span class="dot"></span></div>
  </div>

  <div class="abs brand">
    <span class="mark"></span>
    <span class="name">LUMORA</span>
  </div>

  <nav class="abs nav">
    <a style="left:0">HOME</a>
    <a style="left:65px">OUR TEAM</a>
    <a class="current" style="left:153px">EYE CARE</a>
    <a style="left:234px">MYOPIA CONTROL CLINIC</a>
    <a style="left:412px">EYEWEAR</a>
    <a style="left:493px">BLOG</a>
    <a style="left:554px">CONTACT US</a>
  </nav>
  <svg class="abs search" width="16" height="16" viewBox="0 0 24 24" fill="none" stroke="#0e8cb0" stroke-width="2"><circle cx="10" cy="10" r="7.5"/><path d="M15.5 15.5L22 22"/></svg>

  <div class="abs title-band"><h1>GLAUCOMA</h1></div>
</header>

<main>
  <div class="abs hero" role="img" aria-label="Photo: close-up of a patient's eye with a digital scanning overlay"></div>

  <p class="abs p1 lead">Glaucoma is an eye condition caused by damage to the optic nerve, which is the nerve that connects your eyeball to your brain.</p>
  <p class="abs p2 body">Most of the time, progression of glaucoma is asymptomatic, as it damages peripheral vision first. Since most patients walk around with both eyes open and the two eyes can compensate for each other, patients will not notice symptoms of glaucoma until the severe stages of the disease. If left untreated for long periods of time, a patient may be left with "tunnel vision." This is why routine eye exams are important. Dilated exams allow your eye doctor to obtain an accurate look at your optic nerve, in order to assess if there are signs of damage.</p>
  <p class="abs p3 body">In order to rule out glaucoma in a patient, special testing is required. This testing includes measuring eye pressure, measurements of the optic nerve, a functional test of peripheral vision, and an ocular coherence tomography scan of the nerve. This is how your doctor can look for damage to the nerve that impacts your visual function.</p>
  <p class="abs p4 body">If glaucoma is detected, treatment is initiated in the form of daily eye drops. These eye drops work to lower the pressure inside the eyeball, which takes stress off the optic nerve and prevents further damage. If treated and monitored closely, glaucoma can be very well managed and the patient can maintain good functional vision.</p>
  <p class="abs p5 lead">The key is to catch and manage the condition early, which is why a routine annual exam is always recommended.</p>
</main>

<footer class="abs footer">
  <div class="col" style="left:58px">
    <h2 style="left:0">Lumora Optometry</h2>
    <div class="item" style="top:89px"><span class="ic"><svg width="15" height="14" viewBox="0 0 24 24" fill="#0e8cb0"><path d="M5 2l4 1 1 5-2 2a12 12 0 006 6l2-2 5 1 1 4c-1 1-2 3-5 3C10 22 2 14 2 7c0-3 2-4 3-5z"/></svg></span><span>818-555-0142</span></div>
    <div class="item" style="top:120px"><span class="ic"><svg width="17" height="15" viewBox="0 0 24 20" fill="#0e8cb0"><rect x="0" y="7" width="24" height="13" rx="2"/><rect x="6" y="0" width="12" height="8"/></svg></span><span>818-555-0178</span></div>
    <div class="item" style="top:151px"><span class="ic"><svg width="16" height="12" viewBox="0 0 24 18" fill="#0e8cb0"><rect width="24" height="18" rx="1"/><path d="M1 2l11 8 11-8" stroke="#f9e05c" stroke-width="2" fill="none"/></svg></span><span>info@brivaloka.com</span></div>
    <div class="item" style="top:185px"><span class="ic"><svg width="13" height="17" viewBox="0 0 16 22" fill="#0e8cb0"><path d="M8 0a8 8 0 018 8c0 6-8 14-8 14S0 14 0 8a8 8 0 018-8z"/><circle cx="8" cy="8" r="3" fill="#f9e05c"/></svg></span><span>4820 Corvane Blvd., Delmont,<br>CA 91402</span></div>
    <div class="btn"><span>Get directions on the map</span><svg width="24" height="6" viewBox="0 0 24 6"><path d="M0 3h22M19 0l3 3-3 3" stroke="#0e8cb0" stroke-width="1.5" fill="none"/></svg></div>
  </div>

  <div class="col" style="left:321px">
    <h2 style="left:0">Harrow Glen</h2>
    <div class="item" style="top:89px"><span class="ic"><svg width="15" height="14" viewBox="0 0 24 24" fill="#0e8cb0"><path d="M5 2l4 1 1 5-2 2a12 12 0 006 6l2-2 5 1 1 4c-1 1-2 3-5 3C10 22 2 14 2 7c0-3 2-4 3-5z"/></svg></span><span>818-555-0193</span></div>
    <div class="item" style="top:120px"><span class="ic"><svg width="16" height="12" viewBox="0 0 24 18" fill="#0e8cb0"><rect width="24" height="18" rx="1"/><path d="M1 2l11 8 11-8" stroke="#f9e05c" stroke-width="2" fill="none"/></svg></span><span>harrowglen@brivaloka.com</span></div>
    <div class="item" style="top:150px"><span class="ic"><svg width="13" height="17" viewBox="0 0 16 22" fill="#0e8cb0"><path d="M8 0a8 8 0 018 8c0 6-8 14-8 14S0 14 0 8a8 8 0 018-8z"/><circle cx="8" cy="8" r="3" fill="#f9e05c"/></svg></span><span>11207 Pellard St., Suite 4,<br>Harrow Glen, CA 91408</span></div>
    <div class="btn"><span>Get directions on the map</span><svg width="24" height="6" viewBox="0 0 24 6"><path d="M0 3h22M19 0l3 3-3 3" stroke="#0e8cb0" stroke-width="1.5" fill="none"/></svg></div>
  </div>

  <div class="col" style="left:584px">
    <h2 style="left:0">Opening Hours</h2>
    <div class="hours" style="top:91px;white-space:nowrap">Monday - Thursday : <b>9 am - 6 pm</b></div>
    <div class="hours" style="top:114px;white-space:nowrap">Friday : <b>8.30 am - 5 pm</b></div>
    <div class="hours" style="top:137px;white-space:nowrap">Saturday &nbsp;: <b>8.30 am- 5 pm</b></div>
    <div class="hours" style="top:160px;white-space:nowrap">Closed on <b>Sundays</b></div>
    <div class="hours" style="top:184px;width:190px">Please keep in mind we are closed for <b>lunch 1-2 pm</b></div>
    <span class="social first" style="left:0"><span class="dot"></span></span>
    <span class="social" style="left:38px"><span class="dot"></span></span>
    <span class="social" style="left:76px"><span class="dot"></span></span>
    <span class="social" style="left:115px"><span class="dot"></span></span>
  </div>

  <div class="rule"></div>
  <div class="copy">Copyright © <b>LUMORA OPTOMETRY</b> - 2019 . All right Reserved</div>
</footer>

</body>
</html>
```